New eyelid plastic surgery office needs a business card design-Eyelid Care Partners of the Brenton

I recently used PixelForge for my logo design and was very pleased with creativity and results. It was a difficult decision for me. Now I would like to create a business card based on this logo, which I will attach.

The text should be easily legible as some of my patients have difficulty seeing, but I would like a subtle, sophisticated artistry also evident to make the card memorable. Would like the card based on a similar color scheme as the logo but the inverse or other complementary colors may prove interesting
Updates

A good question was asked...my concern about my visually impaired patients was really my desire to avoid italicized or calligraphic type fonts that may be hard to read. Standard font size for a business card would be fine. Thanks!

Thank you so much for the great work so far. I wanted to give you my particular contact information to see if that would change the look of the cards. Martin Delacourt, MD Address: 2718 Harborview Lane, Suite 206 Wilmington, NC 28517 Phone: 910-555-0193 Fax: 910-555-0194 Website: www.brentonlidstudio.example Please delete the email slot from the card. Thanks so much!

Industry/Entity Type

Plastic

```html
<!DOCTYPE html>
<html lang="en">
<head>
<meta charset="utf-8">
<title>Eyelid Care Partners of the Brenton — Business Card</title>
<link rel="stylesheet" href="https://fonts.googleapis.com/css2?family=Arimo:wght@400;700&display=swap">
<style>
  :root {
    --backdrop: #e6e8ea;
    --card-top: #ffffff;
    --card-bottom: #5ff5f5;
    --band: #33f1f1;
    --band-ornament: #b9dfe6;
    --edge-strip: #c9fbfb;
    --accent-navy: #1f4f9a;
    --brand-navy: #12378a;
    --ink: #111111;
    --rule: #333333;
  }
  * { box-sizing: border-box; margin: 0; padding: 0; }
  html, body { width: 1200px; height: 888px; overflow: hidden; }
  body {
    background: var(--backdrop);
    font-family: "Arimo", Arial, sans-serif;
    display: flex;
    align-items: center;
    justify-content: center;
  }
  .business-card {
    position: relative;
    width: 840px;
    height: 480px;
    background: linear-gradient(180deg, var(--card-top) 0%, var(--card-top) 38%, var(--card-bottom) 100%);
    box-shadow: 0 10px 30px rgba(0,0,0,.18);
    overflow: hidden;
  }
  .brand {
    position: absolute;
    left: 50px;
    top: 62px;
    width: 580px;
    text-align: center;
    color: var(--brand-navy);
    font-weight: 400;
    line-height: 1.05;
    text-transform: uppercase;
  }
  .brand-line-main { display: block; font-size: 52px; letter-spacing: 1px; }
  .brand-line-sub { display: block; font-size: 27px; letter-spacing: 1px; margin-top: 4px; }

  .contact {
    position: absolute;
    left: 58px;
    top: 250px;
    padding-left: 16px;
    border-left: 2px solid var(--rule);
    color: var(--ink);
  }
  .contact-heading { font-size: 14px; font-weight: 700; margin-bottom: 8px; }
  .contact-name { font-size: 22px; font-weight: 700; margin: 0 0 8px 86px; }
  .contact-details {
    display: grid;
    grid-template-columns: 70px auto;
    row-gap: 3px;
    font-size: 15px;
    font-weight: 700;
  }
  .contact-details dt { font-weight: 700; }
  .contact-details dd::before { content: ": "; }

  .ornament-band {
    position: absolute;
    left: 690px;
    top: 0;
    width: 92px;
    height: 100%;
    display: block;
  }
  .edge-strip {
    position: absolute;
    left: 782px;
    top: 0;
    width: 58px;
    height: 100%;
    background: linear-gradient(180deg, #ffffff 0%, var(--edge-strip) 100%);
  }
  .edge-accent {
    position: absolute;
    left: 782px;
    top: 0;
    width: 58px;
    height: 5px;
    background: var(--accent-navy);
  }
</style>
</head>
<body>
  <main class="business-card">
    <h1 class="brand">
      <span class="brand-line-main">Eyelid Care Partners</span>
      <span class="brand-line-sub">of the Brenton</span>
    </h1>

    <section class="contact">
      <p class="contact-heading">Contact :</p>
      <p class="contact-name">Martin Delacourt, MD</p>
      <dl class="contact-details">
        <dt>Address</dt><dd>2718 Harborview Lane, Suite 206 Wilmington, NC 28517</dd>
        <dt>Phone</dt><dd>910 - 555 - 0193</dd>
        <dt>Fax</dt><dd>910 - 555 - 0194</dd>
        <dt>web</dt><dd>www.brentonlidstudio.example</dd>
      </dl>
    </section>

    <svg class="ornament-band" viewBox="0 0 92 480" preserveAspectRatio="none" role="img" aria-label="Vertical band of repeating silver floral ornaments on aqua">
      <defs>
        <linearGradient id="band-fill" x1="0" y1="0" x2="1" y2="0">
          <stop offset="0" stop-color="#33f1f1"/>
          <stop offset="0.5" stop-color="#9fe6ec"/>
          <stop offset="1" stop-color="#33f1f1"/>
        </linearGradient>
      </defs>
      <rect width="92" height="480" fill="url(#band-fill)"/>
    </svg>
    <div class="edge-strip"></div>
    <div class="edge-accent"></div>
  </main>
</body>
</html>
```